Stationery Design Project

I need a design that is simple, clean and modern, in square style, bold font.
The majority of the design needs to be White and Black with a splash of Red colour.
I would like a design for business cards and letter heads with the following information.
Name, Title, Phone, Fax, Email, Website and company ABN number

Target Market(s)

25 to 65 years old real estate clients

Industry/Entity Type

Business

Requirements
Must have
• All designs must incorporate Company Logo, Name, Title, Phone, Fax, Email, Website and company ABN number

```html
<!DOCTYPE html>
<html lang="en">
<head>
<meta charset="utf-8">
<title>Harbour Crest Real Estate – Business Card</title>
<link href="https://fonts.googleapis.com/css2?family=Open+Sans:wght@400;600;700&display=swap" rel="stylesheet">
<style>
  :root {
    --stage: #e9e6e2;
    --card-white: #ffffff;
    --card-black: #231f20;
    --brand-red: #c1272d;
    --ink: #231f20;
    --paper-text: #ffffff;
  }
  * { box-sizing: border-box; margin: 0; padding: 0; }
  html, body {
    width: 1200px; height: 402px; overflow: hidden;
    background: var(--stage);
    font-family: "Open Sans", Arial, sans-serif;
  }
  .stage { position: relative; width: 1200px; height: 402px; }

  .card {
    position: absolute; top: 56px;
    width: 510px; height: 291px; overflow: hidden;
  }
  .card--front { left: 56px; background: var(--card-white); }
  .card--back { left: 638px; background: var(--card-black); }

  .card__wave { position: absolute; inset: 0; width: 510px; height: 291px; }

  .brand-frame {
    position: absolute; border-radius: 16px;
    display: flex; align-items: center; justify-content: center;
  }
  .card--front .brand-frame {
    left: 38px; top: 39px; width: 220px; height: 121px;
    border: 4px solid var(--ink);
  }
  .card--back .brand-frame {
    left: 103px; top: 43px; width: 306px; height: 167px;
    border: 5px solid var(--paper-text); border-radius: 22px;
  }
  .brand-name {
    text-align: center; font-weight: 700; line-height: 1.15;
    text-transform: uppercase;
  }
  .card--front .brand-name { color: var(--ink); font-size: 21px; letter-spacing: 1px; }
  .card--back .brand-name { color: var(--paper-text); font-size: 30px; letter-spacing: 2px; }
  .brand-name__sub { display: block; letter-spacing: 0.45em; }
  .card--front .brand-name__sub { font-size: 12px; margin-top: 6px; }
  .card--back .brand-name__sub { font-size: 16px; margin-top: 10px; }

  .person {
    position: absolute; left: 44px; top: 207px;
    color: var(--brand-red); font-size: 16px; line-height: 20px;
  }
  .person__name { font-weight: 700; }

  .contact-list {
    position: absolute; right: 12px; top: 198px;
    list-style: none; color: var(--paper-text);
    font-size: 12.5px; line-height: 16.5px; text-align: right;
  }
  .contact-list li { display: flex; align-items: center; justify-content: flex-end; gap: 5px; }
  .contact-list svg { width: 10px; height: 10px; fill: var(--paper-text); }

  .address {
    position: absolute; right: 12px; top: 266px;
    color: var(--paper-text); font-size: 13.5px;
  }

  .abn {
    position: absolute; left: 0; right: 0; top: 228px;
    text-align: center; color: var(--paper-text); font-size: 17px;
  }
</style>
</head>
<body>
<main class="stage">

  <section class="card card--front" aria-label="Business card front">
    <svg class="card__wave" viewBox="0 0 510 291" aria-hidden="true">
      <path fill="var(--brand-red)" d="M0,250 C120,252 200,235 260,205 C320,175 380,165 430,166 C470,167 495,175 510,182 L510,291 L0,291 Z"/>
      <path fill="var(--card-white)" d="M0,257 C120,259 200,242 260,212 C320,182 380,172 430,173 C470,174 495,182 510,189 L510,291 L0,291 Z"/>
      <path fill="var(--card-black)" d="M0,262 C120,264 200,247 260,217 C320,187 380,177 430,178 C470,179 495,187 510,194 L510,291 L0,291 Z"/>
    </svg>

    <div class="brand-frame">
      <p class="brand-name">Harbour Crest<span class="brand-name__sub">Real Estate</span></p>
    </div>

    <p class="person"><span class="person__name">Your Name,</span> Title</p>

    <ul class="contact-list">
      <li><svg viewBox="0 0 10 10"><path d="M2 0.5 L3.8 2.6 L2.9 3.8 Q4 6 6.2 7.1 L7.4 6.2 L9.5 8 L8.3 9.5 Q2.5 9 0.5 1.7 Z"/></svg>123-456-7890</li>
      <li><svg viewBox="0 0 10 10"><rect x="1" y="3" width="8" height="6" rx="1"/><rect x="2.5" y="0.5" width="5" height="3" fill="none" stroke="#fff" stroke-width="1"/></svg>123-456-7890</li>
      <li><svg viewBox="0 0 10 10"><rect x="0.5" y="2" width="9" height="6.5"/><path d="M0.5 2 L5 5.5 L9.5 2" fill="none" stroke="#231f20" stroke-width="1"/></svg>info@harbourcrest.com</li>
      <li><svg viewBox="0 0 10 10"><circle cx="5" cy="5" r="4.5"/><path d="M0.5 5 H9.5 M5 0.5 V9.5" stroke="#231f20" stroke-width="0.8"/></svg>www.website.com</li>
    </ul>

    <p class="address">Street Name, City Name, State, City Zip Code</p>
  </section>

  <section class="card card--back" aria-label="Business card back">
    <div class="brand-frame">
      <p class="brand-name">Harbour Crest<span class="brand-name__sub">Real Estate</span></p>
    </div>
    <p class="abn">ABN;123456789</p>
  </section>

</main>
</body>
</html>
```